Specialized Personal Trainer Needs a Business Card Design

I need a business card design for my personal training business called Tall Oak Fitness. I have my Human Kinetics degree in Exercise Science from the Halvering Polytechnic Institute as well as an extra certification from NFBP (National Federation of Body Practice). I work as a Cardiac Rehab Exercise Specialist and personal trainer giving specialized exercise prescriptions to those that have different heart conditions as well as work with the general population in weight loss, strength and conditioning, getting/staying fit.
Updates

I decided that I wanted a logo (as I did not have one before I submitted my project for a business card) so I am submitting a project to get a logo done and then I will decide on a business card, hopefully being able to use one of the designs already submitted.  My apologies for doing this backwards.  I am new to this so I appreciate your patience.

Thank you.

Hi, I have just created a project for a logo design (I realized I needed a logo and I should've done that first..oops!), please feel free to participate.  Once I receive a logo I like I will finalize my business card project and hopefully incorporate it into one of your business card designs. 

Thank you!

Target Market(s)

Business professionals

Industry/Entity Type

Personal Trainer

Requirements
Must have
• My name with my info:
Delphine R. Ashcroft (BHK)
NFBP Certified Clinical Exercise Specialist & Personal Trainer
del.ashcroft@talloakfitness.example
Cell: 555-302-6148

Please make it double sided.
Nice to have
• An image that represents cardiac and general fitness training.

```html
<!DOCTYPE html>
<html lang="en">
<head>
<meta charset="utf-8">
<title>Tall Oak Fitness – Business Card</title>
<link rel="stylesheet" href="https://fonts.googleapis.com/css2?family=Josefin+Sans:wght@300&family=Mulish:wght@400;800&display=swap">
<style>
  :root {
    --page-bg: #e9e7e4;
    --card-bg: #f6f6f4;
    --ink: #222222;
    --ribbon-red: #d6222b;
    --shadow: rgba(0, 0, 0, 0.18);
  }
  html, body {
    margin: 0;
    padding: 0;
    width: 1200px;
    height: 900px;
    overflow: hidden;
    background: var(--page-bg);
  }
  .card {
    position: absolute;
    left: 75px;
    top: 150px;
    width: 1050px;
    height: 600px;
    overflow: hidden;
    background: var(--card-bg);
    box-shadow: 0 10px 30px var(--shadow);
    color: var(--ink);
    font-family: "Mulish", sans-serif;
  }
  .brand-name {
    position: absolute;
    left: 40px;
    top: 70px;
    width: 215px;
    margin: 0;
    text-align: right;
    font-family: "Josefin Sans", sans-serif;
    font-weight: 300;
    font-size: 60px;
    line-height: 1.02;
    color: var(--ink);
  }
  .ribbon {
    position: absolute;
    left: 272px;
    top: 0;
    width: 150px;
    height: 445px;
  }
  .ribbon path { fill: var(--ribbon-red); }
  .holder {
    position: absolute;
    left: 468px;
    top: 258px;
    white-space: nowrap;
  }
  .holder-name {
    margin: 0 0 4px;
    font-weight: 800;
    font-size: 31px;
    letter-spacing: 0.2px;
  }
  .holder-title {
    margin: 0;
    font-weight: 400;
    font-size: 25px;
    line-height: 1.22;
  }
  .contact {
    position: absolute;
    right: 48px;
    top: 455px;
    margin: 0;
    padding: 0;
    list-style: none;
    font-size: 24px;
    white-space: nowrap;
  }
  .contact-item {
    display: flex;
    align-items: center;
    gap: 14px;
    height: 40px;
  }
  .contact-icon {
    width: 20px;
    height: 20px;
    fill: var(--ink);
    flex: none;
  }
</style>
</head>
<body>
  <main class="card">
    <h1 class="brand-name">Tall<br>Oak<br>Fitness</h1>

    <svg class="ribbon" viewBox="0 0 150 445" aria-hidden="true">
      <path d="M0 0 H150 V420 H126 L114 445 L102 420 H0 Z"/>
    </svg>

    <section class="holder">
      <p class="holder-name">Delphine R. Ashcroft (BHK)</p>
      <p class="holder-title">NFBP Certified Clinical Exercise<br>Specialist &amp; Personal Trainer</p>
    </section>

    <ul class="contact">
      <li class="contact-item">
        <svg class="contact-icon" viewBox="0 0 24 24" aria-label="Phone">
          <path d="M6.6 10.8a15.1 15.1 0 0 0 6.6 6.6l2.2-2.2a1 1 0 0 1 1-.25 11.4 11.4 0 0 0 3.6.57 1 1 0 0 1 1 1V20a1 1 0 0 1-1 1A17 17 0 0 1 3 4a1 1 0 0 1 1-1h3.5a1 1 0 0 1 1 1c0 1.25.2 2.45.57 3.57a1 1 0 0 1-.25 1z"/>
        </svg>
        <span>555-302-6148</span>
      </li>
      <li class="contact-item">
        <svg class="contact-icon" viewBox="0 0 24 24" aria-label="Email">
          <path d="M2 5h20v1.2L12 13 2 6.2z"/>
          <path d="M2 8.2l10 6.8 10-6.8V19H2z"/>
        </svg>
        <span>del.ashcroft@talloakfitness.example</span>
      </li>
    </ul>
  </main>
</body>
</html>
```